Verodex business card

Business card for sustainable investment company called "Verodex". Verodex is an exchange platform selling carbon credits between buyers and sellers. Carbon Credits are an environmental commodity for reducing global carbon emissions.

the card should obviously have our logo and the theme should be sustainability/environment mixed with a trading platform.

Contact Information for Business Card

Logo, Name, Title, Phone, Email

Colors
0054AA
0677BA
7BADD7
CADEEF
E8F1F8
0094D4
00A9DD
6FCCEA
C7EBF8
E9F6FB
00AB8E
00BBA5
67D7C9
C6EFE9
E9F9F6
59FF00
82FF00
B8FF75
E3FFCB
F4FFEA

```html
<!DOCTYPE html>
<html lang="en">
<head>
<meta charset="utf-8">
<title>Verodex Business Card</title>
<link href="https://fonts.googleapis.com/css2?family=Montserrat:wght@400;500;700;800&display=swap" rel="stylesheet">
<style>
  :root {
    --bg: #1d1f22;
    --navy: #172a52;
    --blue: #3f7fcf;
    --ink: #1a1a1a;
    --white: #ffffff;
    --cyan: #6acbdb;
    --deep-blue: #4a7cc8;
    --icon: #4a90d0;
  }
  * { margin: 0; padding: 0; box-sizing: border-box; }
  html, body {
    width: 1200px; height: 900px; overflow: hidden;
    background: var(--bg);
    font-family: "Montserrat", Arial, sans-serif;
  }
  .canvas { position: relative; width: 1200px; height: 900px; }
  .card {
    position: absolute;
    width: 640px; height: 366px;
    border-radius: 16px;
    overflow: hidden;
  }
  .card-front { left: 70px; top: 50px; background: var(--white); }
  .card-back { left: 490px; top: 484px; background: var(--navy); }

  .front-wordmark {
    position: absolute; left: 48px; top: 40px;
    font-weight: 800; font-size: 50px; letter-spacing: 1px;
    color: var(--navy); text-transform: uppercase;
  }
  .holder { position: absolute; left: 50px; top: 118px; }
  .holder-name {
    font-weight: 800; font-size: 20px; color: var(--blue);
    text-transform: uppercase; letter-spacing: 1px;
  }
  .holder-title {
    font-weight: 500; font-size: 13px; color: var(--ink);
    text-transform: uppercase; letter-spacing: 1px; margin-top: 2px;
  }
  .address {
    position: absolute; left: 50px; top: 178px;
    font-size: 13px; line-height: 19px; color: var(--ink);
  }
  .contact-list {
    position: absolute; left: 50px; top: 232px;
    list-style: none; font-size: 13px; color: var(--ink);
  }
  .contact-list li { display: flex; align-items: center; gap: 8px; height: 24px; }
  .contact-list svg { width: 14px; height: 14px; flex: none; }
  .front-mark {
    position: absolute; right: 70px; top: 120px;
    width: 170px; height: 170px; border-radius: 50%;
    background: linear-gradient(135deg, var(--cyan), var(--deep-blue));
  }

  .back-brand {
    position: absolute; left: 0; right: 0; top: 0; bottom: 0;
    display: flex; align-items: center; justify-content: center; gap: 18px;
  }
  .back-mark {
    width: 46px; height: 46px; border-radius: 50%;
    background: linear-gradient(135deg, var(--cyan), var(--deep-blue));
  }
  .back-wordmark {
    font-weight: 800; font-size: 54px; letter-spacing: 1px;
    color: var(--white); text-transform: uppercase;
  }
</style>
</head>
<body>
<main class="canvas">
  <section class="card card-front" aria-label="Business card front">
    <div class="front-wordmark">Verodex</div>
    <div class="holder">
      <div class="holder-name">Dana Whitfield</div>
      <div class="holder-title">Manager</div>
    </div>
    <p class="address">2270 Alder Creek Rd. Suite 14<br>Fairhaven, OR 97402</p>
    <ul class="contact-list">
      <li>
        <svg viewBox="0 0 24 24" aria-hidden="true"><path fill="var(--icon)" d="M6.6 10.8a15.1 15.1 0 0 0 6.6 6.6l2.2-2.2a1 1 0 0 1 1-.25 11.4 11.4 0 0 0 3.6.57 1 1 0 0 1 1 1V20a1 1 0 0 1-1 1A17 17 0 0 1 3 4a1 1 0 0 1 1-1h3.5a1 1 0 0 1 1 1c0 1.25.2 2.45.57 3.57a1 1 0 0 1-.25 1z"/></svg>
        555-014-2290
      </li>
      <li>
        <svg viewBox="0 0 24 24" aria-hidden="true"><path fill="var(--icon)" d="M2 5h20v14H2z"/><path fill="none" stroke="#fff" stroke-width="1.6" d="M2 5l10 8 10-8"/></svg>
        hello@verodexmail.com
      </li>
      <li>
        <svg viewBox="0 0 24 24" aria-hidden="true"><circle cx="12" cy="12" r="10" fill="none" stroke="var(--icon)" stroke-width="2"/><path fill="none" stroke="var(--icon)" stroke-width="1.6" d="M2 12h20M12 2c3 3 3 17 0 20M12 2c-3 3-3 17 0 20"/></svg>
        www.verodexsite.com
      </li>
    </ul>
    <div class="front-mark" aria-hidden="true"></div>
  </section>

  <section class="card card-back" aria-label="Business card back">
    <div class="back-brand">
      <div class="back-mark" aria-hidden="true"></div>
      <div class="back-wordmark">Verodex</div>
    </div>
  </section>
</main>
</body>
</html>
```